Business Card Design

Business Card for professional consulting firm working with large financial institutions.

Target Market(s)

Executive buyers

Industry/Entity Type

Banking

Contact Information for Business Card

Mild creativity wanted. Not boring, but do elaborate artwork.

Font styles to use
Serif
Sans Serif

Colors

Designer to choose colors to be used in the design.

Requirements
Must have
• Standard business card features - company name, individual name, telephone, website, email, locations.
Nice to have
• Two colors
Should not have
• too many colors, fancy printing, cartoons.

```html
<!DOCTYPE html>
<html lang="en">
<head>
<meta charset="utf-8">
<title>northpoint — Business Card</title>
<link rel="stylesheet" href="https://fonts.googleapis.com/css2?family=Arvo:wght@400;700&family=Merriweather:wght@400&family=Roboto:wght@400&display=swap">
<style>
  :root {
    --bg: #d9d9d9;
    --paper: #f4f4f4;
    --ink: #111111;
    --text: #444444;
    --muted: #9a9a9a;
    --rule: #222222;
    --night: #1c1d1f;
    --white: #ffffff;
  }
  * { margin: 0; padding: 0; box-sizing: border-box; }
  html, body { width: 1200px; height: 960px; overflow: hidden; }
  body { background: var(--bg); position: relative; }

  .card { position: absolute; width: 602px; height: 343px; }
  .card--front { left: 314px; top: 113px; background: var(--paper); }
  .card--back { left: 311px; top: 472px; width: 600px; background: var(--night);
    display: flex; align-items: center; justify-content: center; }

  .brand-name {
    position: absolute; left: 348px; top: 70px;
    font-family: "Merriweather", Georgia, serif;
    font-size: 26px; color: var(--ink); letter-spacing: 0.2px;
  }
  .person { position: absolute; left: 44px; top: 146px; }
  .person__name {
    font-family: "Arvo", Georgia, serif; font-weight: 700;
    font-size: 20px; color: var(--ink); letter-spacing: 0.5px; line-height: 26px;
  }
  .person__title {
    font-family: "Arvo", Georgia, serif; font-size: 13px;
    color: var(--muted); letter-spacing: 0.3px; line-height: 16px;
  }
  .contacts { position: absolute; left: 44px; top: 206px; list-style: none; }
  .contacts li {
    display: flex; align-items: center; height: 19.5px;
    font-family: "Roboto", Arial, sans-serif; font-size: 14px; color: var(--text);
  }
  .contacts svg { width: 13px; height: 13px; margin-right: 9px; fill: var(--ink); }
  .rule { position: absolute; left: 44px; top: 275px; width: 511px; height: 1.5px; background: var(--rule); }
  .address {
    position: absolute; left: 44px; top: 289px;
    font-family: "Roboto", Arial, sans-serif; font-size: 14px; color: var(--text);
  }
  .back-name {
    font-family: "Merriweather", Georgia, serif;
    font-size: 56px; color: var(--white); letter-spacing: 0.5px;
  }
</style>
</head>
<body>
  <section class="card card--front">
    <div class="brand-name">northpoint</div>
    <div class="person">
      <div class="person__name">DANIEL REYES</div>
      <div class="person__title">CEO/FOUNDER</div>
    </div>
    <ul class="contacts">
      <li><svg viewBox="0 0 24 24" aria-hidden="true"><path d="M6.6 10.8c1.4 2.8 3.8 5.1 6.6 6.6l2.2-2.2c.3-.3.7-.4 1-.2 1.1.4 2.3.6 3.6.6.6 0 1 .4 1 1V20c0 .6-.4 1-1 1C10.6 21 3 13.4 3 4c0-.6.4-1 1-1h3.5c.6 0 1 .4 1 1 0 1.3.2 2.5.6 3.6.1.3 0 .7-.2 1L6.6 10.8z"/></svg>555 310 4826</li>
      <li><svg viewBox="0 0 24 24" aria-hidden="true"><path d="M2 5h20v14H2V5zm2 2v.5l8 5 8-5V7H4zm0 2.8V17h16V9.8l-8 5-8-5z"/></svg>info@northpointadvisory.com</li>
      <li><svg viewBox="0 0 24 24" aria-hidden="true"><path d="M12 2a10 10 0 100 20 10 10 0 000-20zm-1 17.9A8 8 0 014.2 10L9 15v1c0 1.1.9 2 2 2v1.9zm6.9-2.5c-.3-.8-1-1.4-1.9-1.4h-1v-3c0-.6-.4-1-1-1H8v-2h2c.6 0 1-.4 1-1V7h2c1.1 0 2-.9 2-2v-.4a8 8 0 012.9 12.8z"/></svg>www.northpointadvisory.com</li>
    </ul>
    <div class="rule"></div>
    <div class="address">1420 Harbor View Road, Juneau, Alaska 99801</div>
  </section>

  <section class="card card--back">
    <div class="back-name">northpoint</div>
  </section>
</body>
</html>
```